Business Card & Email Signature Design || Upmarket + Luxury

Rima Vale Honey, a New Zealand Manuka Honey company needs a Business Card & Email Signature design.

Our logo's are attached in Gold & Black versions, feel free to be creative with how you use the logo and it's patterns in your design.

Style:
- Looking for an Elegant, Luxurious, Upmarket feel.
- Black/Matte Black Card, Gold Foil, UV Embossing

Information to Add:

- Logo
- Company Name: Rima Vale Honey
- Name: Martin Holloway
- Title: Creative Director
- Phone: +64 2815 96 417
- Email: martin@rimavalehoney.example.nz
- Website: www.rimavalehoney.example.nz

- Socials: ***For email Signature Only***
- Facebook: https://www.facebook.com/rimavalehoney/
- Instagram: https://www.instagram.com/rimavalehoney/

Target Market(s)

Asia/Europe Luxury, Upmarket

Contact Information for Business Card

- Logo
- Name: Martin Holloway
- Phone: +64 2815 96 417

Font styles to use
Other font styles liked:
• Champagne & Limousines (Attached)

Requirements
Must have
• Business Card & Email Signature Design.

Looking for a Sleek, Luxury, Upmarket Design.

```html
<!DOCTYPE html>
<html lang="en">
<head>
<meta charset="utf-8">
<title>Rima Vale Honey — Business Card</title>
<link rel="stylesheet" href="https://fonts.googleapis.com/css2?family=Josefin+Sans:wght@300;400&family=Montserrat:wght@800&family=Arimo:wght@400&display=swap">
<style>
  :root {
    --backdrop: #2a2a2b;
    --card: #0b0b0b;
    --card-edge: #161616;
    --gold: #d9b45a;
    --gold-soft: #b8913f;
    --ink-light: #e9e6df;
    --divider: #2c2c2c;
  }
  * { box-sizing: border-box; margin: 0; padding: 0; }
  html, body {
    width: 1200px; height: 1015px; overflow: hidden;
    background: var(--backdrop);
  }
  .sheet {
    position: relative; width: 1200px; height: 1015px;
    display: flex; flex-direction: column; align-items: center;
    justify-content: center; gap: 60px;
  }
  .card {
    position: relative; width: 760px; height: 434px;
    background: var(--card);
    border: 1px solid var(--card-edge);
    box-shadow: 0 18px 40px rgba(0,0,0,.55);
    overflow: hidden;
  }
  /* back side */
  .card-back .pattern-field {
    position: absolute; inset: 0;
    background: radial-gradient(ellipse at 60% 40%, #1a1a1a 0%, #101010 55%, #0a0a0a 100%);
  }
  .card-back .brand-mark {
    position: absolute; left: 50%; top: 50%;
    transform: translate(-50%, -50%);
    font-family: "Josefin Sans", sans-serif; font-weight: 300;
    font-size: 22px; letter-spacing: 6px; text-transform: uppercase;
    color: var(--gold); white-space: nowrap;
  }
  /* front side */
  .card-front .brand-block {
    position: absolute; left: 0; top: 0; width: 400px; height: 100%;
    display: flex; flex-direction: column; align-items: center; justify-content: center; gap: 22px;
  }
  .card-front .brand-dot {
    width: 56px; height: 56px; border-radius: 50%;
    border: 1.5px solid var(--gold);
  }
  .card-front .brand-name {
    font-family: "Josefin Sans", sans-serif; font-weight: 300;
    font-size: 30px; letter-spacing: 7px; text-transform: uppercase;
    color: var(--gold); white-space: nowrap;
  }
  .card-front .divider {
    position: absolute; left: 408px; top: 120px; width: 1px; height: 190px;
    background: var(--divider);
  }
  .contact {
    position: absolute; left: 440px; top: 120px; width: 300px;
  }
  .contact .person {
    font-family: "Montserrat", sans-serif; font-weight: 800;
    font-size: 22px; letter-spacing: .5px; text-transform: uppercase;
    color: var(--gold); line-height: 1.1;
  }
  .contact .role {
    font-family: "Arimo", sans-serif; font-size: 15px;
    color: var(--ink-light); margin-top: 4px;
  }
  .contact ul { list-style: none; margin-top: 22px; }
  .contact li {
    display: flex; align-items: center; gap: 10px;
    font-family: "Arimo", sans-serif; font-size: 13px;
    color: var(--ink-light); margin-bottom: 10px; white-space: nowrap;
  }
  .contact li.web { color: var(--gold); }
  .contact svg { width: 17px; height: 17px; flex: none; }
</style>
</head>
<body>
<main class="sheet">
  <section class="card card-back" aria-label="Card back">
    <div class="pattern-field" role="img" aria-label="Faint tonal pattern of repeated ornamental bee motifs across the black card"></div>
    <div class="brand-mark">Rima Vale Honey</div>
  </section>

  <section class="card card-front" aria-label="Card front">
    <div class="brand-block">
      <span class="brand-dot"></span>
      <span class="brand-name">Rima Vale Honey</span>
    </div>
    <div class="divider"></div>
    <div class="contact">
      <p class="person">Martin Holloway</p>
      <p class="role">Creative Director</p>
      <ul>
        <li>
          <svg viewBox="0 0 24 24" fill="none" stroke="var(--gold)" stroke-width="2" stroke-linecap="round" stroke-linejoin="round"><path d="M5 3h4l2 5-2.5 1.5a11 11 0 0 0 6 6L16 13l5 2v4a2 2 0 0 1-2 2A16 16 0 0 1 3 5a2 2 0 0 1 2-2z"/></svg>
          +64 2815 96 417
        </li>
        <li>
          <svg viewBox="0 0 24 24" fill="none" stroke="var(--gold)" stroke-width="2" stroke-linejoin="round"><rect x="3" y="5" width="18" height="14"/><path d="M3 5l9 8 9-8"/></svg>
          martin@rimavalehoney.example.nz
        </li>
        <li class="web">
          <svg viewBox="0 0 24 24" fill="none" stroke="var(--gold)" stroke-width="2"><circle cx="12" cy="12" r="9"/><path d="M3 12h18M12 3c3 3 3 15 0 18M12 3c-3 3-3 15 0 18"/></svg>
          www.rimavalehoney.example.nz
        </li>
      </ul>
    </div>
  </section>
</main>
</body>
</html>
```